Design a website for a quickly growing ghostwriting and editing firm

DWB Productions has a website through Wix, but we need help! We are based in Austin, TX, and we work primarily with self-help, wellness, and diet authors. We offer ghostwriting, editing and book development services. You can see our basic site now at www.dorawhitbyproductions.com

```html
<!DOCTYPE html>
<html lang="en">
<head>
<meta charset="utf-8">
<title>DWB Productions — Book Development Services</title>
<link href="https://fonts.googleapis.com/css2?family=Poppins:wght@300;400;500;600;700;800&display=swap" rel="stylesheet">
<style>
:root{
  --orange:#d9822b;
  --orange-dark:#b96a1c;
  --ink:#222;
  --text:#555;
  --muted:#8a8a8a;
  --light:#f1f2f4;
  --hero-a:#e6ebf1;
  --hero-b:#c9d3de;
  --dark:#2c2c2c;
  --dark-2:#363636;
  --footer:#3b3b3b;
  --white:#fff;
}
*{box-sizing:border-box;margin:0;padding:0}
html,body{width:1200px;height:3432px;overflow:hidden}
body{font-family:"Poppins",sans-serif;color:var(--ink);background:var(--white);position:relative}
.abs{position:absolute}
a{color:inherit;text-decoration:none}

/* header */
.site-header{position:absolute;top:0;left:0;width:1200px;height:88px;background:var(--white);z-index:5;display:flex;align-items:center;padding:0 112px}
.brand{display:flex;align-items:center;gap:10px;font-weight:600;font-size:18px;color:var(--ink)}
.brand-mark{width:26px;height:26px;border-radius:50%;background:var(--orange)}
.main-nav{margin-left:auto;display:flex;align-items:center;gap:34px;font-size:13px;font-weight:600;letter-spacing:.5px}
.btn{display:inline-flex;align-items:center;gap:8px;background:var(--orange);color:var(--white);border-radius:30px;font-weight:600;font-size:12px;letter-spacing:.5px;padding:10px 20px}
.btn .arrow{width:16px;height:16px;border-radius:50%;background:var(--white);display:inline-block;position:relative}
.btn .arrow::after{content:"";position:absolute;left:5px;top:5px;width:5px;height:5px;border-top:2px solid var(--orange);border-right:2px solid var(--orange);transform:rotate(45deg)}

/* hero */
.hero{position:absolute;top:0;left:0;width:1200px;height:660px;background:linear-gradient(90deg,var(--hero-a) 0%,#eef1f5 40%,var(--hero-b) 100%);overflow:hidden}
.hero-photo{position:absolute;left:560px;top:88px;width:640px;height:572px;background:linear-gradient(135deg,#d5dde6,#9aa8b8 60%,#55606e)}
.hero-copy{position:absolute;left:112px;top:318px}
.eyebrow{color:var(--orange);font-weight:600;font-size:20px;letter-spacing:.5px}
.hero h1{font-weight:300;font-size:48px;line-height:1.15;color:var(--ink);margin-top:14px;letter-spacing:.5px}
.hero h1 b{font-weight:800}
.hero .btn{margin-top:28px}
.slider-arrows{position:absolute;left:112px;top:620px;display:flex;gap:8px}
.slider-arrows span{width:30px;height:22px;display:block;border:1px solid var(--orange)}
.slider-arrows span.on{background:var(--orange)}
.hero-band{position:absolute;left:0;top:600px}

/* section titles */
.section-title{position:absolute;left:0;width:1200px;text-align:center;font-size:30px;font-weight:700;letter-spacing:1px}

/* work with */
.card{position:absolute;top:848px;background:var(--white);box-shadow:0 4px 14px rgba(0,0,0,.15)}
.card .photo{height:212px}
.card .label{height:60px;display:flex;align-items:center;padding:0 24px;font-weight:600;font-size:18px}
.card.active{border:3px solid var(--orange);top:840px}
.card.active .label{background:var(--orange);color:var(--white);justify-content:space-between;height:72px}

/* about */
.about{position:absolute;top:1210px;left:0;width:1200px;height:540px;background:var(--light)}
.about-photo{position:absolute;left:0;top:1280px;width:540px;height:440px;background:linear-gradient(120deg,#c9a27c,#8b6446 55%,#d8cfc4)}
.about-frame{position:absolute;left:596px;top:1420px;width:410px;height:250px;border:3px solid var(--orange);border-left:none;border-top:none}
.about-copy{position:absolute;left:612px;top:1380px;width:380px}
.about-copy h2{font-size:30px;font-weight:700;letter-spacing:1px}
.about-copy p{font-size:13px;line-height:1.75;color:var(--muted);margin-top:14px}
.btn-outline{display:inline-flex;align-items:center;gap:8px;margin-top:20px;border:2px solid var(--ink);border-radius:30px;padding:8px 16px;font-size:12px;font-weight:600}
.btn-outline .arrow{width:16px;height:16px;border-radius:50%;background:var(--ink);position:relative}
.btn-outline .arrow::after{content:"";position:absolute;left:5px;top:5px;width:5px;height:5px;border-top:2px solid var(--white);border-right:2px solid var(--white);transform:rotate(45deg)}

/* offer */
.offer{position:absolute;top:1780px;left:0;width:1200px;height:500px;background:radial-gradient(ellipse at 50% 40%,var(--dark-2),var(--dark) 70%)}
.offer .section-title{color:var(--white);top:60px}
.service{position:absolute;top:165px;width:300px;text-align:center;color:var(--white)}
.service .icon{width:150px;height:150px;margin:0 auto;border-radius:50%;border:2px solid var(--orange);display:flex;align-items:center;justify-content:center}
.service .icon div{width:124px;height:124px;border-radius:50%;background:var(--orange);display:flex;align-items:center;justify-content:center}
.service h3{font-size:15px;font-weight:600;margin-top:26px;letter-spacing:.5px}
.service p{font-size:12px;line-height:1.6;color:#b5b5b5;margin:10px auto 0;width:240px}

/* blog */
.post-lead{position:absolute;left:112px;top:2460px;width:448px}
.post-lead .photo{height:300px;background:linear-gradient(135deg,#e9d6c3,#b98e6a 60%,#8a6a52);position:relative}
.date{display:inline-block;background:var(--orange);color:var(--white);font-size:12px;font-weight:600;padding:6px 14px}
.post-lead .date{position:absolute;left:0;bottom:0}
.post h3{font-size:17px;font-weight:700;line-height:1.35;margin-top:16px}
.post p{font-size:12px;line-height:1.6;color:var(--muted);margin-top:10px}
.post-side{position:absolute;left:572px;width:516px;display:flex;gap:24px}
.post-side .photo{width:188px;height:196px;flex:none}
.post-side .body{padding-top:20px}
.post-side h3{margin-top:14px}

/* footer */
.site-footer{position:absolute;top:2968px;left:0;width:1200px;height:464px;background:var(--footer);color:var(--white)}
.footer-col{position:absolute;top:128px}
.footer-col h4{font-size:13px;font-weight:700;letter-spacing:.5px;margin-bottom:18px}
.footer-col li{list-style:none;font-size:12px;color:#cfcfcf;margin-bottom:14px;padding-left:16px;position:relative}
.footer-col li::before{content:"";position:absolute;left:0;top:6px;width:5px;height:5px;background:var(--orange)}
.socials{display:flex;gap:8px;margin-bottom:28px}
.socials span{width:28px;height:28px;border-radius:50%;border:1.5px solid var(--white);display:block}
.newsletter{display:flex;width:320px;height:44px;margin-top:4px}
.newsletter .field{flex:1;background:var(--white);color:#999;font-size:12px;display:flex;align-items:center;padding:0 14px}
.newsletter .send{width:48px;background:var(--orange);display:flex;align-items:center;justify-content:center}
.copyright{position:absolute;bottom:0;left:0;width:1200px;height:56px;border-top:1px solid #555;display:flex;align-items:center;justify-content:center;font-size:12px;color:#c7c7c7}
</style>
</head>
<body>

<section class="hero">
  <div class="hero-photo" role="img" aria-label="Smiling man in glasses and suit holding a blank sheet, city skyline behind"></div>
  <div class="hero-copy">
    <div class="eyebrow">DWB PRODUCTION</div>
    <h1>WE PROVIDE <b>BOOK<br>DEVELOPMENT</b><br>SERVICES TO YOU</h1>
    <a class="btn" href="#">GET STARTED <span class="arrow"></span></a>
  </div>
  <div class="slider-arrows"><span></span><span class="on"></span></div>
  <svg class="hero-band" width="1200" height="60" viewBox="0 0 1200 60">
    <polygon points="0,60 1200,4 1200,60" fill="#fff"/>
    <polygon points="620,44 1200,0 1200,14 700,50" fill="#d9822b"/>
  </svg>
</section>

<header class="site-header">
  <div class="brand"><span class="brand-mark"></span>DWB Productions</div>
  <nav class="main-nav">
    <a href="#">HOME</a><a href="#">ABOUT US</a><a href="#">WHAT WE DO</a><a href="#">LATEST BLOG</a><a href="#">CONTACT US</a>
    <a class="btn" href="#">GET STARTED <span class="arrow"></span></a>
  </nav>
</header>

<h2 class="section-title" style="top:770px">WE WORK WITH</h2>

<article class="card" style="left:112px;width:308px">
  <div class="photo" role="img" aria-label="Woman working on a laptop at a bright desk" style="background:linear-gradient(135deg,#f3ede6,#d7c8b8)"></div>
  <div class="label">SELF-HELP</div>
</article>
<article class="card active" style="left:440px;width:320px">
  <div class="photo" role="img" aria-label="Man reading a book at a desk" style="background:linear-gradient(135deg,#eef0f2,#b9a48f)"></div>
  <div class="label">WELLNESS
    <svg width="22" height="18" viewBox="0 0 22 18"><rect x="1" y="1" width="14" height="12" fill="none" stroke="#fff" stroke-width="2"/><path d="M8 8h12M16 4l4 4-4 4" fill="none" stroke="#fff" stroke-width="2"/></svg>
  </div>
</article>
<article class="card" style="left:780px;width:308px">
  <div class="photo" role="img" aria-label="Woman typing on a laptop" style="background:linear-gradient(135deg,#eee7e2,#b86e5c)"></div>
  <div class="label">DIET AUTHORS</div>
</article>

<section class="about"></section>
<svg class="abs" style="left:0;top:1200px" width="1200" height="90" viewBox="0 0 1200 90"><polygon points="0,0 1200,0 1200,10 0,80" fill="#fff"/></svg>
<div class="about-photo" role="img" aria-label="Father and young daughter reading a book together on the floor"></div>
<div class="about-frame"></div>
<div class="about-copy">
  <h2>ABOUT DWB</h2>
  <p>We help experts turn their ideas into finished books. Our writers and editors work closely with you from the first outline to the final draft, keeping your voice clear and your message strong at every stage of the process.</p>
  <a class="btn-outline" href="#">LEARN MORE <span class="arrow"></span></a>
</div>

<section class="offer">
  <h2 class="section-title">WHAT WE OFFER</h2>
  <div class="service" style="left:150px">
    <div class="icon"><div>
      <svg width="56" height="56" viewBox="0 0 56 56" fill="none" stroke="#fff" stroke-width="3"><rect x="10" y="6" width="30" height="42" rx="2"/><path d="M17 16h16M17 24h16M17 32h10"/><path d="M46 18l-12 20-4 6 1-7 12-20z"/></svg>
    </div></div>
    <h3>GHOSTWRITING</h3>
    <p>We write your book in your voice, from first idea to finished manuscript.</p>
  </div>
  <div class="service" style="left:450px">
    <div class="icon"><div>
      <svg width="56" height="56" viewBox="0 0 56 56" fill="none" stroke="#fff" stroke-width="3"><rect x="10" y="10" width="32" height="40" rx="3"/><rect x="19" y="5" width="14" height="9" rx="2"/><path d="M17 24h18M17 32h18M17 40h10"/></svg>
    </div></div>
    <h3>EDITING</h3>
    <p>Careful line and story editing that keeps your message clear and strong.</p>
  </div>
  <div class="service" style="left:750px">
    <div class="icon"><div>
      <svg width="60" height="56" viewBox="0 0 60 56" fill="none" stroke="#fff" stroke-width="3"><path d="M30 14C24 9 14 8 6 10v34c8-2 18-1 24 4 6-5 16-6 24-4V10c-8-2-18-1-24 4z"/><path d="M30 14v34"/></svg>
    </div></div>
    <h3>BOOK DEVELOPMENT SERVICES</h3>
    <p>Structure, outline and coaching to shape your idea into a ready book.</p>
  </div>
</section>

<h2 class="section-title" style="top:2370px">LATEST BLOG POST</h2>

<article class="post post-lead">
  <div class="photo" role="img" aria-label="Young girl reading at a table with an open book"><span class="date">01 JULY, 2021</span></div>
  <h3>LOREM IPSUM DOLOR SIT AMET CONSEC TETUR ADIPISCING</h3>
  <p>Simple habits that help busy authors write a little every single day.</p>
</article>
<article class="post post-side" style="top:2460px">
  <div class="photo" role="img" aria-label="Family reading together on a sofa" style="background:linear-gradient(135deg,#e6dccf,#9c7a5e)"></div>
  <div class="body">
    <span class="date">01 JULY, 2021</span>
    <h3>LOREM IPSUM DOLOR SIT AMET TETUR ADIPISCING</h3>
    <p>How to plan a wellness book readers will finish and share.</p>
  </div>
</article>
<article class="post post-side" style="top:2680px">
  <div class="photo" role="img" aria-label="Older woman reading a book in a bright room" style="background:linear-gradient(135deg,#f0ece6,#b8aa98)"></div>
  <div class="body">
    <span class="date">01 JULY, 2021</span>
    <h3>LOREM IPSUM DOLOR SIT AMET TETUR ADIPISCING</h3>
    <p>Why a clear outline saves months of rewriting later on.</p>
  </div>
</article>

<footer class="site-footer">
  <svg class="abs" style="left:0;top:-20px" width="1200" height="70" viewBox="0 0 1200 70">
    <polygon points="0,20 1200,20 1200,70 0,70" fill="#3b3b3b"/>
    <polygon points="0,20 1200,20 0,70" fill="#fff"/>
    <polygon points="300,40 1200,0 1200,18 420,46" fill="#d9822b"/>
  </svg>
  <div class="footer-col" style="left:144px">
    <h4>QUICK LINKS</h4>
    <ul><li>Home</li><li>About Us</li><li>What we do</li><li>Why Us</li><li>Latest Blog</li></ul>
  </div>
  <div class="footer-col" style="left:320px">
    <h4>SERVICES</h4>
    <ul><li>Ghostwriting</li><li>Editing</li><li>Book development</li></ul>
  </div>
  <div class="footer-col" style="left:528px">
    <h4>OTHER LINKS</h4>
    <ul><li>Terms &amp; Conditions</li><li>Privacy Policy</li><li>Help Service</li><li>FAQ</li><li>Contact us</li></ul>
  </div>
  <div class="footer-col" style="left:744px;top:120px">
    <h4>CONNECTED US ON</h4>
    <div class="socials"><span></span><span></span><span></span><span></span><span></span></div>
    <h4>SUBSCRIBE TO OUR NEWSLETTER</h4>
    <div class="newsletter">
      <div class="field">Email Address</div>
      <div class="send"><svg width="18" height="18" viewBox="0 0 18 18"><path d="M1 8L17 1 11 17 9 10z" fill="#fff"/></svg></div>
    </div>
  </div>
  <div class="copyright">© 2021 DWB Production. All Rights Reserved</div>
</footer>

</body>
</html>
```